Phuket Thailand - Rental Villa Website

I have a villa for rent in Thailand and require a website - i need to demo pictures/walk through video, local attractions, villa facilities description plus seaonal rates and online booking.

Industry/Entity Type

Rental

Coding

Coded - Design and coding required

```html
<!DOCTYPE html>
<html lang="en">
<head>
<meta charset="utf-8">
<title>Villa Rental – Phuket</title>
<link href="https://fonts.googleapis.com/css2?family=Mulish:wght@400;600;700&display=swap" rel="stylesheet">
<style>
:root{
  --green-dark:#4f9d0d;
  --green:#8cc63f;
  --green-text:#79b72a;
  --ink:#222222;
  --text:#333333;
  --muted:#555555;
  --grey-band:#f2f2f2;
  --footer:#e6e6e6;
  --line:#d6d6d6;
  --white:#ffffff;
}
*{box-sizing:border-box;margin:0;padding:0}
html,body{width:1200px;height:2182px;overflow:hidden;background:var(--white);font-family:"Mulish",Arial,sans-serif;color:var(--text)}
.page{position:relative;width:1200px;height:2182px}
.abs{position:absolute}
.backdrop{left:0;top:0}
/* header */
.site-header{left:172px;top:35px;width:855px;height:93px;border-radius:12px;background:linear-gradient(#ffffff,#e4e4e4);box-shadow:0 10px 8px -4px rgba(0,0,0,.45)}
.brand{position:absolute;left:16px;top:28px;font-size:29px;font-weight:600;color:var(--ink);white-space:nowrap}
.main-nav{position:absolute;left:0;top:0;width:855px;height:93px;font-size:12.5px;font-weight:600;color:var(--ink)}
.main-nav a{position:absolute;top:38px;color:inherit;text-decoration:none;white-space:nowrap;line-height:16px}
.main-nav .active{top:35px;left:282px;width:73px;height:22px;line-height:22px;text-align:center;background:var(--green);color:var(--white);border-radius:11px}
.search-btn{position:absolute;left:803px;top:28px;width:36px;height:36px;border-radius:50%;background:#333}
/* hero */
.hero{left:172px;top:154px;width:855px;height:437px;background:var(--white);padding:7px}
.hero-media{width:842px;height:428px;background:linear-gradient(90deg,#5a4a3c 0%,#cfc6b8 35%,#e8e4dc 55%,#9a8d66 72%,#bfc4cf 100%);position:relative}
.play{position:absolute;left:381px;top:175px}
.dots{position:absolute;left:389px;top:396px;display:flex;gap:5px}
.dots span{width:9px;height:9px;border-radius:50%;background:#fff}
/* headings */
.section-title{color:var(--green-text);font-weight:400;font-size:28px;text-align:center;width:1200px;left:0}
/* booking */
.booking-shadow{left:200px;top:700px;width:800px;height:14px;background:radial-gradient(ellipse at top,rgba(0,0,0,.08),transparent 70%)}
.field{height:28px;border:1px solid var(--line);background:#fff;font-size:10px;color:#666;padding:7px 7px;width:270px}
.btn{display:flex;align-items:center;justify-content:center;color:#fff;font-size:11px;font-weight:700}
.btn-green{background:var(--green)}
.btn-dark{background:var(--ink)}
/* attractions */
.band{left:0;top:854px;width:1200px;height:676px;background:var(--grey-band)}
.band-title{font-size:28px;font-weight:400;color:var(--green-text)}
.photo{width:270px;height:166px}
.caption{width:275px;font-size:10.5px;line-height:14px;color:#333}
.detail-btn{width:83px;height:25px}
/* facilities */
.facilities{left:758px;top:899px;width:269px;height:590px;background:var(--green);color:#fff;padding:28px 22px 0 22px}
.facilities h2{font-size:27px;font-weight:400;margin-bottom:18px}
.facilities p{font-size:12px;line-height:18px;padding-right:2px}
.facilities ul{list-style:none;margin-top:48px}
.facilities li{font-size:12.5px;height:28.4px;display:flex;gap:12px;white-space:nowrap}
.facilities li::before{content:"»";font-weight:700}
.more-btn{left:782px;top:1424px;width:206px;height:25px;background:var(--ink);color:#fff;font-size:13px;display:flex;align-items:center;justify-content:center}
/* rates */
.intro{left:172px;top:1624px;width:855px;text-align:center;font-size:13px;line-height:23px;color:var(--ink)}
.rates{left:172px;top:1684px;width:855px;border-collapse:collapse}
.rates th{background:var(--green);color:#fff;font-weight:400;font-size:18px;height:54px;border-right:1px solid #a9d66d}
.rates th:first-child{text-align:left;padding-left:19px}
.rates td{height:87px;background:linear-gradient(#ffffff,#e9e9e9);border:1px solid #e0e0e0;text-align:center}
.villa{text-align:left!important;padding-left:11px}
.villa .box{display:inline-block;width:14px;height:14px;border:1px solid #ccc;background:#f4f4f4;vertical-align:top;margin-right:12px;margin-top:4px}
.villa .name{display:inline-block;font-size:18px;color:var(--ink)}
.villa small{display:block;font-size:10px;color:var(--green-text)}
.price{font-size:27px;color:var(--ink);line-height:30px}
.night{font-size:18px;color:var(--green-text)}
.row-btn{margin:0 auto;width:83px;height:35px;font-size:13px}
/* footer */
.site-footer{left:0;top:2048px;width:1200px;height:134px;background:var(--footer)}
.social{position:absolute;left:517px;top:27px;display:flex;gap:9px}
.social span{width:18px;height:18px;background:#222;border-radius:3px}
.foot-nav{position:absolute;top:60px;width:1200px;text-align:center;font-size:13px;color:var(--ink);word-spacing:2px}
.foot-nav span{margin:0 18px}
.copyright{position:absolute;top:91px;width:1200px;text-align:center;font-size:13px;color:var(--ink)}
</style>
</head>
<body>
<div class="page">
  <svg class="abs backdrop" width="1200" height="520" viewBox="0 0 1200 520" aria-hidden="true">
    <polygon points="0,0 1200,0 1200,342 1027,436 172,440 0,415" fill="#4f9d0d"/>
    <polygon points="0,415 172,425 172,480 0,509" fill="#8cc63f"/>
    <polygon points="1027,436 1200,342 1200,502 1027,487" fill="#a6d36b"/>
  </svg>

  <header class="abs site-header">
    <div class="brand">Villa Rental</div>
    <nav class="main-nav">
      <a class="active">Home</a>
      <a style="left:368px">About Us</a>
      <a style="left:451px">Seasonal Rates</a>
      <a style="left:567px">Local Attractions</a>
      <a style="left:689px">Villa Facilities</a>
    </nav>
    <div class="search-btn">
      <svg width="36" height="36" viewBox="0 0 36 36"><circle cx="16" cy="16" r="5" fill="none" stroke="#fff" stroke-width="2.2"/><line x1="20" y1="20" x2="24" y2="24" stroke="#fff" stroke-width="2.5"/></svg>
    </div>
  </header>

  <section class="abs hero">
    <div class="hero-media" role="img" aria-label="Walk-through video of the villa bedroom with desk, artwork and bed">
      <svg class="play" width="80" height="80" viewBox="0 0 80 80"><circle cx="40" cy="40" r="35" fill="none" stroke="#fff" stroke-width="7"/><polygon points="31,24 58,40 31,56" fill="#fff"/></svg>
      <div class="dots"><span></span><span></span><span></span><span></span><span></span></div>
    </div>
  </section>

  <h2 class="abs section-title" style="top:645px">Online Booking</h2>
  <div class="abs booking-shadow"></div>
  <form class="booking">
    <div class="abs field" style="left:172px;top:736px">First Name</div>
    <div class="abs field" style="left:464px;top:736px">E-Mail Address</div>
    <div class="abs field" style="left:756px;top:736px">Phone</div>
    <div class="abs field" style="left:172px;top:777px">Address</div>
    <div class="abs field" style="left:464px;top:777px">Telephone</div>
    <div class="abs btn btn-green" style="left:756px;top:777px;width:118px;height:27px">Book Now</div>
    <div class="abs btn btn-dark" style="left:881px;top:777px;width:86px;height:27px">Clear</div>
  </form>

  <div class="abs band"></div>
  <h2 class="abs band-title" style="left:176px;top:922px">Local Attractions</h2>
  <svg class="abs" style="left:688px;top:932px" width="46" height="20" viewBox="0 0 46 20"><path d="M2 10h14M2 10l7-7M2 10l7 7" stroke="#222" stroke-width="3.5" fill="none"/><path d="M44 10H30M44 10l-7-7M44 10l-7 7" stroke="#222" stroke-width="3.5" fill="none"/></svg>

  <div class="abs photo" style="left:172px;top:980px;background:linear-gradient(135deg,#3f6a2a,#a8c98c 55%,#3f7f8a)" role="img" aria-label="Limestone cliffs and green bay"></div>
  <div class="abs photo" style="left:464px;top:980px;background:linear-gradient(#3b74c6,#a9c8e8 50%,#5d8f2f 70%,#3f6a1e)" role="img" aria-label="Elephant ride in front of ancient temple ruins"></div>
  <p class="abs caption" style="left:172px;top:1155px">Neque porro quisquam est qui dolorem ipsum quia dolor sit amet, consectetur, adipisci velit...</p>
  <p class="abs caption" style="left:464px;top:1155px">Neque porro quisquam est qui dolorem ipsum quia dolor sit amet, consectetur, adipisci velit...</p>
  <div class="abs btn btn-green detail-btn" style="left:172px;top:1197px">View Details</div>
  <div class="abs btn btn-green detail-btn" style="left:464px;top:1197px">View Details</div>

  <div class="abs photo" style="left:172px;top:1247px;background:linear-gradient(#0d0f1c,#2b1c25 60%,#b5652a)" role="img" aria-label="Temple at night with floating lanterns"></div>
  <div class="abs photo" style="left:464px;top:1247px;background:linear-gradient(135deg,#1d3f7a,#c8962f 50%,#6e4a16)" role="img" aria-label="Golden pagoda and temple statues"></div>
  <p class="abs caption" style="left:172px;top:1425px">Neque porro quisquam est qui dolorem ipsum quia dolor sit amet, consectetur, adipisci velit...</p>
  <p class="abs caption" style="left:464px;top:1425px">Neque porro quisquam est qui dolorem ipsum quia dolor sit amet, consectetur, adipisci velit...</p>
  <div class="abs btn btn-green detail-btn" style="left:172px;top:1465px">View Details</div>
  <div class="abs btn btn-green detail-btn" style="left:464px;top:1465px">View Details</div>

  <aside class="abs facilities">
    <h2>Villa Facilities</h2>
    <p>Lorem Ipsum is simply dummy text of the printing and typesetting industry. Lorem Ipsum has been the industry's standard dummy text ever since the 1500s, when an unknown printer took a galley of type and scrambled it to make a type specimen book.</p>
    <ul>
      <li>Lorem ipsum dolor sit amet,</li>
      <li>Consectetur adipiscing elit,</li>
      <li>Sed do eiusmod tempor</li>
      <li>Incididunt ut labore et</li>
      <li>Dolore magna aliqua.</li>
      <li>Ut enim ad minim veniam,</li>
      <li>Quis nostrud exercitation ullamco</li>
      <li>Laboris nisi ut aliquip</li>
    </ul>
  </aside>
  <div class="abs more-btn">View More Facilities</div>

  <h2 class="abs section-title" style="top:1566px">Seasonal Rates</h2>
  <p class="abs intro">Lorem Ipsum is simply dummy text of the printing and typesetting industry. Lorem Ipsum has been the industry's standard dummy text ever since the 1500s, when an unknown printer took a galley of type and scrambled it to make a type specimen book.</p>

  <table class="abs rates">
    <colgroup><col style="width:269px"><col style="width:228px"><col style="width:228px"><col style="width:130px"></colgroup>
    <thead><tr><th>Price For 2015</th><th>Low Season</th><th>High Season</th><th>Info</th></tr></thead>
    <tbody>
      <tr><td class="villa"><span class="box"></span><span class="name">1 Bedroom Villas<small>For 2 people</small></span></td>
        <td><div class="price">$ 250/week</div><div class="night">($ 150/night)</div></td>
        <td><div class="price">$550/week</div><div class="night">($ 150/night)</div></td>
        <td><div class="btn btn-green row-btn">Book Now</div></td></tr>
      <tr><td class="villa"><span class="box"></span><span class="name">2 Bedroom Villas<small>For 4 people</small></span></td>
        <td><div class="price">$ 250/week</div><div class="night">($ 150/night)</div></td>
        <td><div class="price">$ 550/week</div><div class="night">($ 150/night)</div></td>
        <td><div class="btn btn-green row-btn">Book Now</div></td></tr>
      <tr><td class="villa"><span class="box"></span><span class="name">3 Bedroom Villas<small>For 6 people</small></span></td>
        <td><div class="price">$ 250/week</div><div class="night">($ 150/night)</div></td>
        <td><div class="price">$ 550/week</div><div class="night">($ 150/night)</div></td>
        <td><div class="btn btn-green row-btn">Book Now</div></td></tr>
    </tbody>
  </table>

  <footer class="abs site-footer">
    <div class="social" aria-label="Social links"><span></span><span></span><span></span><span></span><span></span><span></span></div>
    <div class="foot-nav">Home<span>|</span>About Us<span>|</span>Seasonal Rates<span>|</span>Local Attractions<span>|</span>Villa Facilities</div>
    <div class="copyright">©2014 Company Name ,All Rights Reserved</div>
  </footer>
</div>
</body>
</html>
```